Building company buisness cards

We are looking for a sharp modern new look for our business cards.We are a New Zealand based company that specialises in house and land packages.We have attached a photo of the current logo and would like to see if it can be improved somehow if needed.We are open to any colours but we have chosen Black and White at this stage. Feel free to change the font and make the logo smarter looking.Play with the colours and see what looks best.We want a card that looks so good know one will want to throw it away!

Target Market(s)

Building profesonals, home buyers

Industry/Entity Type

Building

Contact Information for Business Card

Garrick Tenwood
0275390628
garrickt@hartvale.co.nz

Font styles to use
Serif
Sans Serif

Colors

Designer to choose colors to be used in the design.

Requirements
Must have
• Just the logo on one side and details on the other
• Clean simple looking card
Nice to have
• Round corners and detail like raised or spot UV
• Something that stands out
Should not have
• To title needed, Director etc

```html
<!DOCTYPE html>
<html lang="en">
<head>
<meta charset="utf-8">
<title>Hartvale Business Cards</title>
<link rel="stylesheet" href="https://fonts.googleapis.com/css2?family=Abril+Fatface&family=Open+Sans:wght@300;400;700&display=swap">
<style>
  :root {
    --stage: #2b2b2d;
    --card-black: #111112;
    --card-white: #ffffff;
    --ink: #151515;
    --silver: #d9d9d9;
    --muted: #8a8a8a;
    --faint: #ececec;
  }
  * { margin: 0; padding: 0; box-sizing: border-box; }
  html, body { width: 1200px; height: 885px; overflow: hidden; }
  body {
    background: var(--stage);
    font-family: "Open Sans", Arial, sans-serif;
    position: relative;
  }
  .card {
    position: absolute;
    width: 600px;
    height: 343px;
    border-radius: 22px;
    overflow: hidden;
  }
  /* Logo side */
  .card--logo {
    left: 150px; top: 70px;
    background: linear-gradient(160deg, #1c1c1e 0%, var(--card-black) 70%);
  }
  .card--logo .brand {
    position: absolute;
    left: 0; right: 0; top: 108px;
    display: flex; align-items: center; justify-content: center; gap: 16px;
  }
  .card--logo .brand-circle {
    width: 34px; height: 34px;
    border: 3px solid var(--silver);
    border-radius: 50%;
  }
  .card--logo .brand-name {
    color: var(--silver);
    font-weight: 300;
    font-size: 46px;
    letter-spacing: 4px;
  }
  .card--logo .web {
    position: absolute;
    left: 0; right: 0; top: 258px;
    text-align: center;
    color: var(--silver);
    font-size: 14px;
    letter-spacing: 7px;
  }
  /* Details side */
  .card--details {
    left: 450px; top: 470px;
    background: var(--card-white);
  }
  .card--details .watermark {
    position: absolute;
    right: -70px; top: -80px;
    width: 300px; height: 300px;
    border: 14px solid var(--faint);
    border-radius: 50%;
  }
  .card--details .brand {
    position: absolute;
    left: 44px; top: 56px;
    display: flex; align-items: center; gap: 10px;
  }
  .card--details .brand-name {
    font-family: "Abril Fatface", Georgia, serif;
    font-size: 50px;
    color: var(--ink);
    line-height: 1;
  }
  .card--details .brand-circle {
    width: 34px; height: 34px;
    border: 3px solid var(--ink);
    border-radius: 50%;
  }
  .contact {
    position: absolute;
    left: 44px; top: 176px;
    list-style: none;
    color: var(--muted);
    font-size: 17px;
    line-height: 24px;
  }
  .contact li { display: flex; align-items: center; gap: 10px; }
  .contact svg { width: 14px; height: 14px; fill: var(--ink); flex: none; }
  .name-band {
    position: absolute;
    left: 0; bottom: 0;
    width: 600px; height: 80px;
  }
  .name-band svg { position: absolute; inset: 0; }
  .name-band .name {
    position: absolute;
    left: 54px; bottom: 22px;
    color: #fff;
    font-weight: 700;
    font-size: 21px;
  }
</style>
</head>
<body>
  <section class="card card--logo">
    <div class="brand">
      <span class="brand-name">Hartvale</span>
      <span class="brand-circle"></span>
    </div>
    <p class="web">www.Hartvale.co.nz</p>
  </section>

  <section class="card card--details">
    <div class="watermark"></div>
    <div class="brand">
      <span class="brand-name">Hartvale</span>
      <span class="brand-circle"></span>
    </div>
    <ul class="contact">
      <li>
        <svg viewBox="0 0 16 16"><path d="M3 1h3l1 4-2 1c1 2 3 4 5 5l1-2 4 1v3c0 1-1 2-2 2C7 15 1 9 1 3c0-1 1-2 2-2z"/></svg>
        0275390628
      </li>
      <li>
        <svg viewBox="0 0 16 16"><path d="M1 3h14v10H1z M2 4l6 5 6-5" fill="none" stroke="#151515" stroke-width="1.6"/></svg>
        garrickt@hartvale.co.nz
      </li>
      <li>
        <svg viewBox="0 0 16 16"><circle cx="8" cy="8" r="7"/><path d="M1 8h14M8 1c3 3 3 11 0 14M8 1c-3 3-3 11 0 14" fill="none" stroke="#fff" stroke-width="1"/></svg>
        www.hartvale.co.nz
      </li>
    </ul>
    <div class="name-band">
      <svg viewBox="0 0 600 80" preserveAspectRatio="none">
        <path d="M0 22 H36 L46 0 L50 22 H600 V80 H0 Z" fill="#111112"/>
      </svg>
      <span class="name">Garrick Tenwood</span>
    </div>
  </section>
</body>
</html>
```